Business Postcard Design for Personal Training Company

Need a postcard design for my company called "Copperleaf Studio" Colors are Navy Blue, Blue, Grey and White.

On the front I want there to be pictures and it to feature a box that says "Free Consultation + 50% off your first session!"

And somehow to feature the following phrases " Lose Weight. Gain Muscle."
"Customized Personal training using Q-Pulse, the latest technology in fitness. Reach your fitness goals in just two 25-min sessions per week"

Also want featured the following phrases (maybe on back):

"up to 18 times more effective than a conventional gym workout"

I need the back of the postcard to have all my business information:

Address: 287 Wendover Ln, Building D Suite 318, Costa Mesa CA 92631
Website: copperleaf-studio.example
Phone #: (949) 555-0137
E-mail: copperleafwellness@mailbox.example

I am going to upload my logo, before and after pictures and pictures of people training on the device. Feel free to use as many/or little photos as you want.

Target Market(s)

Wealthy Adults 40+ years old looking for a personal trainer

Industry/Entity Type

Personal Trainer

Colors
0455a3
85cae6
aaaaaa
ffffff

Requirements
Must have
• At least two of the before and after photos, and two or more photos of people working out on the device.

```html
<!DOCTYPE html>
<html lang="en">
<head>
<meta charset="utf-8">
<title>Copperleaf Studio – Postcards</title>
<link href="https://fonts.googleapis.com/css2?family=Open+Sans:wght@400;600;700;800&display=swap" rel="stylesheet">
<style>
  :root {
    --navy: #0b4a94;
    --navy-deep: #083a78;
    --blue: #0455a3;
    --sky: #85cae6;
    --grey: #aaaaaa;
    --grey-light: #eeeeee;
    --ink: #3a3a3a;
    --white: #ffffff;
    --stage: #e4e4e2;
  }
  * { box-sizing: border-box; margin: 0; padding: 0; }
  html, body { width: 833px; height: 1200px; overflow: hidden; }
  body { background: var(--stage); font-family: "Open Sans", Arial, sans-serif; }
  .stage { position: relative; width: 833px; height: 1200px; }

  .card {
    position: absolute; left: 96px; width: 640px; height: 495px;
    background: var(--white); overflow: hidden;
    box-shadow: 0 6px 14px rgba(0,0,0,.22);
  }
  .card--front { top: 70px; }
  .card--back  { top: 635px; }

  .photo { position: absolute; }
  .shape { position: absolute; left: 0; top: 0; }

  .brand { position: absolute; display: flex; align-items: center; gap: 8px;
    color: var(--blue); font-weight: 700; font-size: 17px; letter-spacing: .2px; }
  .brand__dot { width: 26px; height: 26px; border-radius: 50%; background: var(--sky); }

  /* front */
  .front__photo { left: 0; top: 0; width: 360px; height: 400px;
    background: linear-gradient(160deg, #cfd3d9 0%, #9aa6b4 35%, #2b3d66 65%, #3b4d86 100%); }
  .front__brand { left: 405px; top: 38px; }
  .headline { position: absolute; left: 280px; width: 360px; top: 107px; text-align: center;
    color: var(--navy); font-weight: 700; font-size: 19px; }
  .offer { position: absolute; left: 290px; top: 142px; width: 350px; text-align: center;
    color: var(--white); font-weight: 700; font-size: 22.5px; line-height: 31px; }
  .intro { position: absolute; left: 310px; width: 310px; top: 232px; text-align: center;
    color: var(--ink); font-size: 14.5px; line-height: 24.5px; white-space: nowrap; }
  .snapshot { position: absolute; left: 478px; top: 338px; width: 140px; height: 98px;
    background: var(--white); padding: 5px; transform: rotate(3deg);
    box-shadow: 0 2px 6px rgba(0,0,0,.3); display: flex; gap: 4px; }
  .snapshot__half { flex: 1; position: relative;
    background: linear-gradient(180deg, #b8a08c, #3a3b45); }
  .snapshot__half--after { background: linear-gradient(180deg, #c7b09d, #4d5060); }
  .snapshot__label { position: absolute; bottom: 4px; width: 100%; text-align: center;
    color: var(--white); font-size: 7px; font-weight: 700; }

  .address { position: absolute; left: 32px; top: 421px; color: var(--white);
    font-size: 13.5px; line-height: 18.5px; }
  .contact { position: absolute; color: var(--navy); font-size: 14.5px; line-height: 22px; white-space: nowrap; }
  .contact strong { font-weight: 700; }
  .contact .phone { font-size: 17px; font-weight: 700; padding: 0 4px; }
  .front__contact { left: 232px; top: 424px; }

  /* back */
  .back__brand { left: 30px; top: 50px; }
  .circle { position: absolute; width: 122px; height: 122px; border-radius: 50%;
    border: 5px solid var(--sky); }
  .circle--one { left: 373px; top: 25px; background: linear-gradient(180deg, #c9d6e2 0%, #7f8f74 60%, #5f6b58 100%); }
  .circle--two { left: 499px; top: 25px; background: linear-gradient(180deg, #d8d8d4 0%, #6a6f7a 60%, #3c3f48 100%); }
  .tagline { position: absolute; left: 0; top: 135px; width: 350px; text-align: center;
    color: var(--white); font-weight: 700; font-size: 12.5px; line-height: 17px; }
  .back__photo { left: 0; top: 181px; width: 372px; height: 200px;
    background: linear-gradient(180deg, #e6e6e6 0%, #b9b9bb 50%, #4a4d57 100%); }
  .compare { top: 120px; height: 261px; }
  .compare--before { left: 374px; width: 129px; background: linear-gradient(180deg, #e8e6e2 0%, #c8a890 45%, #2a2a30 100%); }
  .compare--after { left: 505px; width: 135px; background: linear-gradient(180deg, #dcdcda 0%, #c3a288 45%, #25252b 100%); }
  .compare__label { position: absolute; bottom: 6px; left: 10px; color: var(--white);
    font-size: 9px; font-weight: 700; letter-spacing: .3px; }
  .back__contact { left: 236px; width: 398px; top: 408px; text-align: center;
    font-size: 15px; line-height: 23px; }
  .back__contact .phone { font-size: 18px; }
</style>
</head>
<body>
<div class="stage">

  <!-- Front -->
  <section class="card card--front">
    <div class="photo front__photo" role="img" aria-label="Trainer guiding a client wearing an electrode suit on an exercise ball"></div>
    <svg class="shape" width="640" height="495" viewBox="0 0 640 495" aria-hidden="true">
      <defs>
        <linearGradient id="panelFade" x1="0" y1="0" x2="0" y2="1">
          <stop offset="0" stop-color="#f0f0f0"/>
          <stop offset=".35" stop-color="#ffffff"/>
        </linearGradient>
      </defs>
      <path d="M300 0 Q240 200 290 400 L640 400 L640 0 Z" fill="url(#panelFade)"/>
      <polygon points="292,135 640,135 640,211 280,211" fill="var(--navy)"/>
      <rect x="0" y="403" width="210" height="92" fill="var(--navy)"/>
      <polygon points="194,389 640,389 640,495 211,495" fill="var(--sky)"/>
    </svg>

    <div class="brand front__brand"><span class="brand__dot"></span>Copperleaf Studio</div>
    <h1 class="headline">LOSE WEIGHT. GAIN MUSCLE.</h1>
    <p class="offer">FREE CONSULTATION<br>+ 50% off your first session!</p>
    <p class="intro">Customized Personal training using<br>Q-Pulse, the latest technology in fitness.<br>Reach your fitness goals in just two<br>25-min sessions per week</p>

    <div class="snapshot">
      <div class="snapshot__half" role="img" aria-label="Client before training"><span class="snapshot__label">BEFORE</span></div>
      <div class="snapshot__half snapshot__half--after" role="img" aria-label="Client after training"><span class="snapshot__label">AFTER</span></div>
    </div>

    <p class="address">287 Wendover Ln,<br>Building D Suite 318,<br>Costa Mesa CA 92631</p>
    <p class="contact front__contact">Call <span class="phone">(949) 555-0137</span> today<br>Or visit <strong>copperleaf-studio.example</strong> for information.</p>
  </section>

  <!-- Back -->
  <section class="card card--back">
    <div class="brand back__brand"><span class="brand__dot"></span>Copperleaf Studio</div>
    <div class="circle circle--one" role="img" aria-label="Outdoor training session overlooking the coast"></div>
    <div class="circle circle--two" role="img" aria-label="Two clients training in the studio"></div>

    <div class="photo back__photo" role="img" aria-label="Trainer coaching a client doing a side plank in an electrode suit"></div>
    <div class="photo compare compare--before" role="img" aria-label="Client before the program"><span class="compare__label">BEFORE</span></div>
    <div class="photo compare compare--after" role="img" aria-label="Client after the program"><span class="compare__label">AFTER</span></div>

    <svg class="shape" width="640" height="495" viewBox="0 0 640 495" aria-hidden="true">
      <path d="M0 112 L330 112 Q345 112 352 128 L0 128 Z" fill="var(--grey-light)"/>
      <polygon points="0,129 335,129 352,181 0,181" fill="var(--navy)"/>
      <path d="M372 181 Q330 280 372 381 L372 181 Z" fill="var(--white)"/>
      <rect x="0" y="381" width="640" height="8" fill="var(--white)"/>
      <rect x="0" y="400" width="215" height="95" fill="var(--navy)"/>
      <polygon points="194,389 640,389 640,495 228,495" fill="var(--sky)"/>
    </svg>

    <p class="tagline">UP TO 18 TIMES MORE EFFECTIVE<br>THAN A CONVENTIONAL GYM WORKOUT</p>

    <p class="address">287 Wendover Ln,<br>Building D Suite 318,<br>Costa Mesa CA 92631</p>
    <p class="contact back__contact">Call <span class="phone">(949) 555-0137</span> today<br>Or visit <strong>copperleaf-studio.example</strong> for information.<br>Email <strong>copperleafwellness@mailbox.example</strong></p>
  </section>

</div>
</body>
</html>
```